Business Cards for IT Consulting Company (Managed Service Provider)

I am looking to have some business cards printed and would like some designs. We are an IT Consulting company based in Vancouver BC. I would like a nice clean and modern look to the cards. I have uploaded all the versions of my logo so parts can be used as needed. Here is a snippit from our website homepage:

Quillbrook Networks Ltd. is an IT Solutions Partner located in Vancouver BC, Canada. We offer IT solutions and support to customers in the greater Vancouver Area. With expertise in Microsoft platforms, as well as Linux and Mac OSX and over 12 years experience in the IT industry, Quillbrook Networks is dedicated to offering our clients top quality service and products. We take pride in the solutions we offer our customers. The greatest compliment a client can give us is to recommend our services.

Quillbrook Networks Ltd. offers a wide range of IT services from onsite service to remote support and managed service solutions. This allows clients to choose the support path that best suits their company’s needs. Supporting many different sized companies from small to enterprise level over the past 12 years Quillbrook Networks has the experience and expertise needed to ensure things run smoothly. Allowing our clients to focus on doing business.

Revolutionizing the way IT services are delivered.

Quillbrook Networks is dedicated to providing our clients with IT solutions that work and grow with them for years to come. This philosophy helps save money in the long run instead of replacing equipment constantly. Far too often IT solutions are not well thought out and while possibly solving the problem at hand, require replacement due to growth or quality within a very short time frame. Quillbrook Networks takes pride in providing solutions that will last and be able to accommodate growth without the need for replacement.

Industry/Entity Type

Information Technology

Contact Information for Business Card

Quillbrook Networks Ltd.
(Employee Name)
Eml: (Employees Email Address)
Web: quillbrook.me
Ph: 604-555-0148

Font styles to use
Serif
Sans Serif

Requirements
Must have
• The Company logo and company colors.
Nice to have
• - Our tag line: "Revolutionizing IT Services" or "Revolutionizing the way IT services are delivered."
• - Also I really like the idea of nature and technology together blending which is sort of where my logo came from so integrating that somehow onto the business cards would be great.

```html
<!DOCTYPE html>
<html lang="en">
<head>
<meta charset="utf-8">
<title>Quillbrook Networks Ltd. — Business Cards</title>
<link rel="stylesheet" href="https://fonts.googleapis.com/css2?family=Montserrat:wght@500;600;700&family=Roboto:ital,wght@0,400;1,400&display=swap">
<style>
  :root {
    --backdrop: #a9a7a7;
    --card-dark: #1f1f20;
    --card-light: #f3f3f3;
    --brand-blue: #1f8fd6;
    --text-light: #e6e6e6;
    --text-dark: #3f3f3f;
    --text-muted: #555555;
  }
  * { margin: 0; padding: 0; box-sizing: border-box; }
  html, body {
    width: 1200px; height: 1200px; overflow: hidden;
    background: var(--backdrop);
  }
  .canvas { position: relative; width: 1200px; height: 1200px; }

  .card { position: absolute; width: 713px; height: 419px; }
  .card--front { left: 238px; top: 117px; background: var(--card-dark); }
  .card--back { left: 230px; top: 643px; background: var(--card-light); }

  .wordmark {
    position: absolute;
    font-family: "Montserrat", sans-serif;
    font-weight: 600;
    color: var(--brand-blue);
    white-space: nowrap;
    letter-spacing: 0.2px;
  }
  .card--front .wordmark { left: 0; right: 0; top: 160px; text-align: center; font-size: 34px; }
  .card--back .wordmark { left: 22px; top: 80px; font-size: 29px; }

  .tagline {
    position: absolute; left: 0; right: 0; top: 376px;
    display: flex; align-items: center; justify-content: center; gap: 16px;
    font-family: "Montserrat", sans-serif; font-weight: 500; font-size: 18px;
    color: var(--text-light);
  }
  .tagline__rule { width: 110px; height: 3px; background: var(--brand-blue); }

  .accent-bar {
    position: absolute; left: 692px; top: 60px; width: 19px; height: 97px;
    background: var(--brand-blue);
  }

  .person { position: absolute; left: 136px; top: 188px; }
  .person__name {
    font-family: "Montserrat", sans-serif; font-weight: 700; font-size: 25px;
    color: var(--brand-blue);
  }
  .person__role {
    margin-top: 6px;
    font-family: "Roboto", sans-serif; font-style: italic; font-size: 16px;
    color: var(--text-muted);
  }

  .contact { position: absolute; left: 136px; top: 279px; list-style: none; }
  .contact__item {
    display: flex; align-items: center; height: 27.5px;
    font-family: "Roboto", sans-serif; font-size: 18px; color: var(--text-dark);
  }
  .contact__icon { width: 18px; height: 16px; margin-right: 17px; flex: none; }
</style>
</head>
<body>
<main class="canvas">

  <section class="card card--front" aria-label="Card front">
    <div class="wordmark">Quillbrook Networks Ltd.</div>
    <div class="tagline">
      <span class="tagline__rule"></span>
      <span>Revolutionizing IT Services</span>
      <span class="tagline__rule"></span>
    </div>
  </section>

  <section class="card card--back" aria-label="Card back">
    <div class="wordmark">Quillbrook Networks Ltd.</div>
    <div class="accent-bar"></div>

    <div class="person">
      <div class="person__name">Dana Whitfield</div>
      <div class="person__role">Managing Director</div>
    </div>

    <ul class="contact">
      <li class="contact__item">
        <svg class="contact__icon" viewBox="0 0 18 16" aria-hidden="true">
          <path d="M2 4 Q9 0 16 4 L15 6 L12 5.5 L12 4 Q9 3 6 4 L6 5.5 L3 6 Z" fill="#1f8fd6"/>
          <rect x="3" y="8" width="12" height="7" rx="1.5" fill="#1f8fd6"/>
          <circle cx="9" cy="11.5" r="2" fill="#f3f3f3"/>
        </svg>
        604-555-0148
      </li>
      <li class="contact__item">
        <svg class="contact__icon" viewBox="0 0 18 16" aria-hidden="true">
          <g fill="none" stroke="#1f8fd6" stroke-width="1.4">
            <circle cx="9" cy="8" r="6.5"/>
            <ellipse cx="9" cy="8" rx="3" ry="6.5"/>
            <line x1="2.5" y1="8" x2="15.5" y2="8"/>
            <line x1="3.5" y1="4.5" x2="14.5" y2="4.5"/>
            <line x1="3.5" y1="11.5" x2="14.5" y2="11.5"/>
          </g>
        </svg>
        www.quillbrook.me
      </li>
      <li class="contact__item">
        <svg class="contact__icon" viewBox="0 0 18 16" aria-hidden="true">
          <rect x="1" y="3" width="16" height="11" fill="#1f8fd6"/>
          <path d="M1.5 3.5 L9 9.5 L16.5 3.5" fill="none" stroke="#f3f3f3" stroke-width="1.4"/>
        </svg>
        support@quillbrook.me
      </li>
    </ul>
  </section>

</main>
</body>
</html>
```